Small environmental consultancy needs a simple but professional web design

We are a boutique environmental consultancyand contracting business located in Margaret River in the South West of Western Australia.

We have two arms
1) Consulting which offers environmental planning, management and assessment services primarily to local government and the development industry.
2) Contracting which implements on site plans and on ground works primarily involving revegetation, bush regeneration and environmental weed control.

We need a simple yet professional web design within the wordpress platform that commmunicates professionalism, experience and technical expertise without appearing too corporate.

Something like this structure appeals:
http://fernquill.net.au/environment-services/
or
http://www.tallowbrookenvironmental.com.au/index.php

(without the image gallery function)

Target Market(s)

Local Government Officers deciding on tenders;
Developers, Engineers, Town Planning consultants looking for environmental expertise

Industry/Entity Type

Business

Number of Pages Required

5+ page

Font styles to use
Sans Serif

Colors
33a6d7
9bcb3c

Requirements
Must have
• Pages required include:
• Home
• Environmental Planning and Management
• Revegetation and Regeneration Implementation (This page can mirror the Environmental Planning and Management page exactly in structure but with different text and images)
• About Us (I think that this page can be relatively simple and generic)
• Contact (I think that this page can be very simple and generic)
Nice to have
• An ability to start out basic and quicikly establish a website presence and then build in additional drop downs and pages over time.
Should not have
• It does not need a photo gallery page;
• It does not need a major amount of space dedicated to social media and blogs etc as this is not currently particularly active area for us

```html
<!DOCTYPE html>
<html lang="en">
<head>
<meta charset="utf-8">
<title>Kestrel Ecoservices – Environmental Consultants</title>
<link rel="stylesheet" href="https://fonts.googleapis.com/css2?family=Oswald:wght@400;500&family=Source+Sans+3:wght@400&family=Raleway:wght@400;500&display=swap">
<style>
:root{
  --black:#000;
  --footer:#1b1b1b;
  --green:#9bcb3c;
  --blue:#33a6d7;
  --white:#fff;
  --paper:#e6e6e6;
  --text:#555;
  --muted:#6d6d6d;
  --icon:#bdbdbd;
}
*{box-sizing:border-box;margin:0;padding:0}
html,body{width:872px;height:1200px;overflow:hidden;background:var(--white)}
body{position:relative;font-family:"Source Sans 3",sans-serif}
a{color:inherit;text-decoration:none}

.site-header{position:absolute;left:0;top:0;width:872px;height:116px;background:var(--black)}
.brand{position:absolute;left:56px;top:58px;display:flex;align-items:center;gap:8px}
.brand-mark{width:22px;height:22px;border-radius:50%;background:var(--green)}
.brand-name{font-family:"Oswald",sans-serif;font-weight:400;font-size:19px;color:var(--green);letter-spacing:.5px}
.utility{position:absolute;right:54px;top:12px;display:flex;align-items:center;gap:14px;color:var(--icon)}
.utility svg{display:block}
.utility .phone{display:flex;align-items:center;gap:6px;font-family:"Source Sans 3",sans-serif;font-size:18px;color:var(--icon)}
.main-nav{position:absolute;right:53px;top:82px;display:flex;gap:14px;font-family:"Oswald",sans-serif;font-size:15px;color:var(--white);text-transform:uppercase}

.hero{position:absolute;left:0;top:116px;width:872px;height:436px;
  background:linear-gradient(180deg,#5f8fc4 0%,#93b6d6 38%,#3e5a2f 58%,#4f7a2a 72%,#6a9a34 100%)}
.hero-title{position:absolute;left:0;right:0;top:164px;text-align:center;font-family:"Oswald",sans-serif;font-weight:500;font-size:58px;letter-spacing:8px;color:var(--white);line-height:1}
.hero-sub{position:absolute;left:0;right:0;top:230px;text-align:center;font-family:"Oswald",sans-serif;font-size:29px;letter-spacing:3px;color:var(--white);line-height:1}

.feature-band{position:absolute;left:0;top:552px;width:872px;height:198px;background:var(--paper)}
.feature-card{position:absolute;top:27px;width:177px;height:145px}
.feature-card .photo{position:absolute;inset:0}
.feature-card .label{position:absolute;left:0;right:0;top:47px;height:51px;background:rgba(20,20,20,.55);
  font-family:"Oswald",sans-serif;font-weight:500;font-size:26px;line-height:23px;letter-spacing:2px;color:var(--white);
  text-align:center;padding-top:3px;text-transform:uppercase}
.card-why{left:54px}.card-why .photo{background:linear-gradient(160deg,#2d5a20,#b8352a 60%,#2b4a1c)}
.card-services{left:250px}.card-services .photo{background:linear-gradient(180deg,#3a6bb8,#6f8b5a 50%,#3c5a24)}
.card-project{left:446px}.card-project .photo{background:linear-gradient(180deg,#7c8a6a,#4b6a2c 60%,#5e8a2a)}
.card-contact{left:642px}.card-contact .photo{background:linear-gradient(160deg,#2f5a1e,#c2452a 55%,#3a6a22)}
.slider-arrow{position:absolute;top:80px}
.slider-prev{left:18px}.slider-next{right:18px}

.welcome{position:absolute;left:54px;top:782px;width:570px}
.welcome-mark{position:absolute;left:4px;top:6px;width:38px;height:38px;border-radius:50%;background:var(--green)}
.welcome-heading{margin-left:61px;font-family:"Raleway",sans-serif;line-height:1}
.welcome-heading .intro{display:block;font-size:17px;color:#333}
.welcome-heading .name{display:block;margin-top:3px;font-size:24px;font-weight:500;color:var(--green)}
.welcome-copy{margin-top:25px;font-size:12.4px;line-height:16px;color:var(--text)}
.welcome-copy p+p{margin-top:16px}
.welcome-photo{position:absolute;left:642px;top:796px;width:176px;height:175px;
  background:radial-gradient(circle at 50% 48%,#2f8a3a 0 22%,#b98a6a 23% 48%,#7fb43a 60%,#3f7a22 100%)}

.site-footer{position:absolute;left:0;top:1068px;width:872px;height:132px;background:var(--footer);color:var(--white)}
.footer-contact{position:absolute;left:0;right:0;top:26px;display:flex;justify-content:center;align-items:center;gap:34px;font-size:11.5px}
.footer-contact .item{display:flex;align-items:center;gap:7px}
.footer-mark{width:34px;height:34px;border-radius:50%;background:var(--green)}
.footer-nav{position:absolute;left:0;right:0;top:74px;display:flex;justify-content:center;gap:15px;font-family:"Oswald",sans-serif;font-size:11.5px;letter-spacing:.3px;text-transform:uppercase}
.copyright{position:absolute;left:0;right:0;top:103px;text-align:center;font-family:"Oswald",sans-serif;font-size:10.5px;letter-spacing:.4px;color:var(--muted);text-transform:uppercase}
</style>
</head>
<body>

<header class="site-header">
  <a class="brand" href="#">
    <span class="brand-mark"></span>
    <span class="brand-name">Kestrel Ecoservices</span>
  </a>
  <div class="utility">
    <svg width="18" height="16" viewBox="0 0 18 16" aria-label="Home"><path d="M9 0 0 8h2.5v8h5v-5h3v5h5V8H18z" fill="currentColor"/></svg>
    <svg width="18" height="14" viewBox="0 0 18 14" aria-label="Email"><rect width="18" height="14" rx="1.5" fill="currentColor"/><path d="M1 1.5 9 8l8-6.5" stroke="#000" stroke-width="1.6" fill="none"/></svg>
    <span class="phone">
      <svg width="13" height="15" viewBox="0 0 13 15"><path d="M3 0 5.5 4 4 5.6c.8 2 2.2 3.4 4 4.3L9.5 8.5 13 11l-1.6 3C5 13.4 .5 8 1 1.5z" fill="#9bcb3c"/></svg>
      (808) 555 01 2746
    </span>
    <svg width="17" height="17" viewBox="0 0 17 17" aria-label="Search"><circle cx="7" cy="7" r="5.2" stroke="currentColor" stroke-width="2" fill="none"/><path d="M11 11l5 5" stroke="currentColor" stroke-width="2.2"/></svg>
  </div>
  <nav class="main-nav">
    <a href="#">Environmental Planning &amp; Management</a>
    <a href="#">Revegetation &amp; Regeneration Implementation</a>
    <a href="#">About Us</a>
  </nav>
</header>

<section class="hero" role="img" aria-label="Large tree standing in a green meadow under a blue sky">
  <h1 class="hero-title">KESTREL ECOSERVICES</h1>
  <p class="hero-sub">ENVIRONMENTAL CONSULTANTS</p>
</section>

<section class="feature-band">
  <svg class="slider-arrow slider-prev" width="26" height="46" viewBox="0 0 26 46"><path d="M24 2 3 23l21 21" stroke="#c4c4c4" stroke-width="3" fill="none"/></svg>
  <a class="feature-card card-why" href="#"><span class="photo" role="img" aria-label="Red tropical flowers among green leaves"></span><span class="label">Why<br>Kestrel?</span></a>
  <a class="feature-card card-services" href="#"><span class="photo" role="img" aria-label="Red flowers against a blue sky"></span><span class="label">Our<br>Services</span></a>
  <a class="feature-card card-project" href="#"><span class="photo" role="img" aria-label="Sunlit forest with green undergrowth"></span><span class="label">Current<br>Project</span></a>
  <a class="feature-card card-contact" href="#"><span class="photo" role="img" aria-label="Red and orange flowers with foliage"></span><span class="label">Contact<br>Us</span></a>
  <svg class="slider-arrow slider-next" width="26" height="46" viewBox="0 0 26 46"><path d="M2 2l21 21L2 44" stroke="#c4c4c4" stroke-width="3" fill="none"/></svg>
</section>

<section class="welcome">
  <span class="welcome-mark"></span>
  <h2 class="welcome-heading"><span class="intro">Welcome to</span><span class="name">KESTREL ECOSERVICES</span></h2>
  <div class="welcome-copy">
    <p>Lorem ipsum dolor sit amet, consectetur adipiscing elit, sed do eiusmod tempor incididunt ut labore et dolore magna aliqua. Ut enim ad minim veniam, quis nostrud exercitation ullamco laboris nisi ut aliquip ex ea commodo consequat. Duis aute irure dolor in reprehenderit in voluptate velit esse cillum dolore eu fugiat nulla pariatur. Excepteur sint occaecat cupidatat non proident, sunt in culpa qui officia deserunt mollit anim id est laborum.</p>
    <p>Duis aute irure dolor in reprehenderit in voluptate velit esse cillum dolore eu fugiat nulla pariatur. Excepteur sint occaecat cupidatat non proident, sunt in culpa qui officia deserunt mollit anim id est laborum.</p>
  </div>
</section>
<div class="welcome-photo" role="img" aria-label="Cupped hands holding a green globe wrapped in leaves"></div>

<footer class="site-footer">
  <div class="footer-contact">
    <span class="item"><svg width="9" height="11" viewBox="0 0 13 15"><path d="M3 0 5.5 4 4 5.6c.8 2 2.2 3.4 4 4.3L9.5 8.5 13 11l-1.6 3C5 13.4 .5 8 1 1.5z" fill="#9bcb3c"/></svg>(808) 555 01 2746</span>
    <span class="footer-mark"></span>
    <span class="item"><svg width="11" height="9" viewBox="0 0 18 14"><rect width="18" height="14" rx="1.5" fill="#9bcb3c"/><path d="M1 1.5 9 8l8-6.5" stroke="#1b1b1b" stroke-width="1.8" fill="none"/></svg>INFO@KESTRELECOSERVICES.COM</span>
  </div>
  <nav class="footer-nav">
    <a href="#">Home</a>
    <a href="#">Environmental Planning &amp; Management</a>
    <a href="#">Revegetation &amp; Regeneration Implementation</a>
    <a href="#">About Us</a>
    <a href="#">Contact</a>
  </nav>
  <p class="copyright">© 2015 Kestrel Ecoservices. &nbsp;All rights reserved</p>
</footer>

</body>
</html>
```